RTavenor Business Cards & Letterhead

I have a logo but need a design for some new business cards. We are a Design-Build Firm that specializes in the design and construction of commercial projects.
the cards need to be professional. no cartoon stuff.
i would like to have the cards in AI format so I can update the card as needed. Logo is provided.
Our Address is: 4187 Marlowe Ct. Alderwick, South Dakota 27614

```html
<!DOCTYPE html>
<html lang="en">
<head>
<meta charset="utf-8">
<title>RTavenor Business Card</title>
<link rel="stylesheet" href="https://fonts.googleapis.com/css2?family=Open+Sans:wght@400;700&display=swap">
<style>
  :root {
    --stage: #7b7c80;
    --card-front: #ffffff;
    --card-back: #55565b;
    --ink: #4a4b4f;
    --ink-soft: #5c5d61;
    --brand-blue: #1a6fb8;
    --rule: #8a8b8f;
    --white: #ffffff;
  }
  * { box-sizing: border-box; margin: 0; padding: 0; }
  html, body { width: 1200px; height: 781px; overflow: hidden; }
  body {
    background: var(--stage);
    font-family: "Open Sans", Verdana, sans-serif;
    display: flex;
    align-items: center;
    justify-content: center;
    gap: 60px;
  }
  .card {
    width: 510px;
    height: 292px;
    border-radius: 18px;
    position: relative;
    overflow: hidden;
    box-shadow: 0 10px 28px rgba(0,0,0,0.25);
  }
  .card--front { background: var(--card-front); }
  .card--back {
    background: var(--card-back);
    display: flex;
    align-items: center;
    justify-content: center;
  }
  .wordmark {
    display: flex;
    align-items: center;
    gap: 10px;
    font-weight: 700;
    letter-spacing: 0.5px;
    text-transform: uppercase;
    white-space: nowrap;
  }
  .wordmark__square { width: 16px; height: 16px; background: var(--brand-blue); }
  .card--front .wordmark {
    position: absolute;
    left: 32px;
    top: 44px;
    font-size: 34px;
    color: var(--ink);
  }
  .card--back .wordmark { font-size: 44px; color: var(--white); }
  .card--back .wordmark__square { width: 20px; height: 20px; }
  .divider {
    position: absolute;
    left: 250px;
    top: 122px;
    width: 1.5px;
    height: 140px;
    background: var(--rule);
  }
  .contact {
    position: absolute;
    left: 268px;
    top: 120px;
    right: 16px;
    color: var(--ink-soft);
    font-size: 12.5px;
    line-height: 19px;
    white-space: nowrap;
  }
  .contact__name {
    color: var(--brand-blue);
    font-weight: 700;
    font-size: 20px;
    line-height: 24px;
    text-transform: uppercase;
    letter-spacing: 0.3px;
  }
  .contact__row { display: flex; align-items: center; gap: 6px; }
  .contact__row svg { width: 11px; height: 11px; flex: none; }
</style>
</head>
<body>
  <section class="card card--front" aria-label="Business card front">
    <div class="wordmark"><span class="wordmark__square"></span>RTavenor</div>
    <div class="divider"></div>
    <div class="contact">
      <p class="contact__name">Rowan Tavenor</p>
      <p>President</p>
      <p>4187 Marlowe Ct. Alderwick,</p>
      <p>South Dakota 27614</p>
      <p class="contact__row">
        <svg viewBox="0 0 12 12"><path d="M3 1l2 2-1 1.5c.6 1.4 1.6 2.4 3 3L8.5 6.5l2 2L9 10.5C5 10 2 7 1.5 3z" fill="var(--brand-blue)"/></svg>
        555-555-0148
      </p>
      <p class="contact__row">
        <svg viewBox="0 0 12 12"><rect x="1" y="2.5" width="10" height="7" fill="var(--brand-blue)"/><path d="M1 2.5l5 4 5-4" stroke="#fff" fill="none"/></svg>
        Quotes@RTavenor.com
      </p>
      <p class="contact__row">
        <svg viewBox="0 0 12 12"><circle cx="6" cy="6" r="5" fill="var(--brand-blue)"/><path d="M1 6h10M6 1c2 2 2 8 0 10M6 1c-2 2-2 8 0 10" stroke="#fff" stroke-width=".7" fill="none"/></svg>
        www.RTavenor.com
      </p>
    </div>
  </section>
  <section class="card card--back" aria-label="Business card back">
    <div class="wordmark"><span class="wordmark__square"></span>RTavenor</div>
  </section>
</body>
</html>
```